Website Design Request - Management Consulting Firm

We need a Website designed for an IT Management Staffing and Recruiting firm called TRAVENOK based in San Francisco.

The firm is an high-end technology staffing agency. Our focus is on quality and high-caliber candidates rather than quantity.

The website will have two main home pages. One for the recruiter and another on for the candidates.

The website needs to optimize for mobile devices as well.

I have attached few mock-ups that I have done just to show what I am thinking. The UI needs to be very clean, fluid, and it needs to have a modern, rustic, professional feel to it.

Target Market(s)

Technology Manager, Director, VP, CIO of Companies that have $4b-10b dollar revenue. Such as larkspurdwellings.example , https://www.velmorian.example/, quillnet.example, zib.example

Industry/Entity Type

Management Consulting

Number of Pages Required

5+ page

Font styles to use
Sans Serif

Colors
f37122
ffffff

Requirements
Must have
• Please review mock-ups for suggestions
Nice to have
Should not have

```html
<!DOCTYPE html>
<html lang="en">
<head>
<meta charset="utf-8">
<title>TRAVENOK – IT Project Management Jobs</title>
<link rel="stylesheet" href="https://fonts.googleapis.com/css2?family=Open+Sans:wght@400;600;700;800&display=swap">
<style>
:root{
  --orange:#f37122;
  --orange-dark:#d95f14;
  --white:#ffffff;
  --ink:#3a3a3a;
  --muted:#777777;
  --page:#ececec;
  --footer:#efefef;
  --footer-bar:#dcdcdc;
  --tab-dark:#3d3d3d;
  --hero-a:#4a4d52;
  --hero-b:#2c2f33;
}
*{box-sizing:border-box;margin:0;padding:0}
html,body{width:813px;height:1200px;overflow:hidden;background:var(--page)}
body{font-family:"Open Sans",Arial,sans-serif;color:var(--ink);position:relative}

/* Header */
.site-header{position:absolute;left:0;top:0;width:813px;height:82px;background:var(--white);border-bottom:1px solid #e2e2e2}
.brand{position:absolute;left:26px;top:16px}
.brand-name{font-size:34px;font-weight:800;color:var(--orange);letter-spacing:1px;line-height:36px;white-space:nowrap}
.brand-tag{font-size:8px;font-weight:700;color:var(--ink);letter-spacing:.6px;margin-top:2px;white-space:nowrap}
.main-nav{position:absolute;right:22px;top:30px;display:flex;gap:6px}
.main-nav a{font-size:11px;font-weight:600;color:var(--ink);text-decoration:none;padding:6px 9px;border:1px solid transparent}
.main-nav a.active{border-color:#bdbdbd;color:var(--orange)}

/* Hero */
.hero{position:absolute;left:0;top:82px;width:813px;height:218px;background:linear-gradient(135deg,var(--hero-a),var(--hero-b))}
.hero-arrow{position:absolute;top:92px}
.hero-arrow.left{left:16px}.hero-arrow.right{right:16px}
.hero-title{position:absolute;left:50%;transform:translateX(-50%);top:60px;background:var(--orange);color:var(--white);font-size:25px;font-weight:700;padding:6px 18px;white-space:nowrap}
.hero-sub{position:absolute;width:100%;top:112px;text-align:center;color:var(--white);font-size:16px;font-weight:600}
.signup{position:absolute;left:210px;top:143px;display:flex;gap:8px}
.signup .field{width:254px;height:30px;background:var(--hero-b);border:1px solid #666;color:#cfcfcf;font-size:11px;padding:8px 10px}
.btn{background:var(--orange);color:var(--white);font-size:11px;font-weight:700;padding:8px 12px;display:inline-block}
.hero-note{position:absolute;width:100%;top:188px;text-align:center;color:var(--white);font-size:12px}
.hero-note span{text-decoration:underline}

/* Steps card */
.steps-card{position:absolute;left:65px;top:383px;width:683px;height:508px;background:var(--white);border:1px solid #dcdcdc}
.tabs{display:flex;height:36px}
.tab{flex:1;display:flex;align-items:center;justify-content:center;color:var(--white);font-size:14px;font-weight:700}
.tab.active{background:var(--orange);position:relative}
.tab.active::after{content:"";position:absolute;bottom:-8px;left:50%;margin-left:-8px;border:8px solid transparent;border-bottom:0;border-top-color:var(--orange)}
.tab.dark{background:var(--tab-dark)}
.steps-kicker{text-align:center;font-size:12px;margin-top:22px}
.steps-headline{text-align:center;font-size:18px;color:var(--orange);font-weight:600;margin-top:6px}
.step-list{position:absolute;left:26px;top:130px;width:320px;list-style:none}
.step{display:flex;gap:14px;margin-bottom:22px}
.step-num{flex:none;width:28px;height:28px;border-radius:50%;background:var(--orange);color:var(--white);font-weight:700;font-size:14px;display:flex;align-items:center;justify-content:center;margin-top:6px}
.step-title{color:var(--orange);font-size:14px;font-weight:600}
.step-text{font-size:11px;color:var(--muted);margin-top:2px;line-height:15px}
.upload-btn{position:absolute;left:68px;top:372px;display:flex;align-items:center;gap:8px}
.team-illustration{position:absolute;left:362px;top:150px;width:290px;height:250px;background:radial-gradient(circle at 50% 55%,#f4c9a8,#fbe9dc 60%,var(--white))}
.scroll-down{position:absolute;left:388px;top:899px;width:38px;height:38px;border-radius:50%;background:var(--orange);display:flex;align-items:center;justify-content:center}

/* Footer */
.site-footer{position:absolute;left:0;top:960px;width:813px;height:240px;background:var(--footer)}
.footer-brand{position:absolute;left:40px;top:44px;width:190px}
.footer-brand .brand-name{font-size:27px;line-height:30px;letter-spacing:.5px}
.footer-brand .brand-tag{font-size:6.5px;letter-spacing:.4px}
.socials{display:flex;gap:7px;margin-top:14px}
.socials span{width:20px;height:20px;border-radius:50%;border:2px solid var(--ink)}
.footer-col{position:absolute;top:18px}
.footer-col h3{font-size:12px;font-weight:700;color:var(--orange);padding-bottom:6px;border-bottom:1px solid #cfcfcf;margin-bottom:10px}
.contact-col{left:246px;width:170px}
.contact-item{display:flex;gap:10px;margin-bottom:10px}
.contact-icon{flex:none;width:26px;height:26px;border-radius:50%;background:var(--orange);display:flex;align-items:center;justify-content:center}
.contact-item p{font-size:9px;line-height:12px;color:var(--ink)}
.contact-item b{font-size:10px}
.links-col{left:436px;width:128px}
.links-col ul{list-style:none}
.links-col li{font-size:10px;margin-bottom:5px;display:flex;align-items:center;gap:6px}
.links-col li::before{content:"";width:5px;height:5px;border-radius:50%;background:var(--orange)}
.form-col{left:584px;width:170px}
.form-row{display:flex;gap:6px;margin-bottom:6px}
.input{flex:1;height:22px;background:var(--white);border:1px solid #cfcfcf;font-size:9px;color:var(--muted);padding:5px 6px}
.textarea{height:48px;background:var(--white);border:1px solid #cfcfcf;font-size:9px;color:var(--muted);padding:5px 6px;margin-bottom:8px}
.form-col .btn{font-size:9px;padding:6px 10px}
.footer-bar{position:absolute;left:0;bottom:0;width:813px;height:30px;background:var(--footer-bar);text-align:center;font-size:10px;line-height:30px;color:var(--ink)}
</style>
</head>
<body>
<header class="site-header">
  <div class="brand">
    <div class="brand-name">TRAVENOK</div>
    <div class="brand-tag">PROJECT MANAGEMENT CONSULTATION</div>
  </div>
  <nav class="main-nav">
    <a class="active">HOME</a><a>PROFESSIONALS</a><a>EMPLOYERS</a><a>SIGN IN</a><a>SIGN UP</a><a>CONTACT</a>
  </nav>
</header>

<section class="hero" role="img" aria-label="Team of professionals working around an office meeting table">
  <svg class="hero-arrow left" width="14" height="30" viewBox="0 0 14 30"><path d="M12 2 L2 15 L12 28" fill="none" stroke="#fff" stroke-width="2.5"/></svg>
  <svg class="hero-arrow right" width="14" height="30" viewBox="0 0 14 30"><path d="M2 2 L12 15 L2 28" fill="none" stroke="#fff" stroke-width="2.5"/></svg>
  <h1 class="hero-title">LOOKING FOR IT PROJECT MANAGEMENT JOBS?</h1>
  <p class="hero-sub">Upload your resume, accept interview requests, get offers</p>
  <div class="signup"><div class="field">Your Email Address</div><div class="btn">GET OFFERS NOW</div></div>
  <p class="hero-note">Looking for talents? <span>See how it works for employers</span></p>
</section>

<section class="steps-card">
  <div class="tabs"><div class="tab active">HOW IT WORKS?</div><div class="tab dark">WHY US?</div></div>
  <p class="steps-kicker">3 Simple steps</p>
  <h2 class="steps-headline">Employers pay 25% more for a better FIT Project Manager</h2>
  <ol class="step-list">
    <li class="step"><span class="step-num">1</span><div><div class="step-title">Upload your resume</div><div class="step-text">Answer few questions and upload your resume.</div></div></li>
    <li class="step"><span class="step-num">2</span><div><div class="step-title">We send you interview requests</div><div class="step-text">Interested in someone? With a single click, send interview request and let us handle the rest.</div></div></li>
    <li class="step"><span class="step-num">3</span><div><div class="step-title">Get $1000 Bonus</div><div class="step-text">Find a job and get $1000 bonus TRAVENOK</div></div></li>
  </ol>
  <div class="btn upload-btn">
    <svg width="12" height="12" viewBox="0 0 12 12"><path d="M6 1 V8 M3 4 L6 1 L9 4 M1 11 H11" fill="none" stroke="#fff" stroke-width="1.6"/></svg>
    UPLOAD YOUR RESUME
  </div>
  <div class="team-illustration" role="img" aria-label="Illustration of a job interview with a candidate facing a panel of interviewers"></div>
</section>

<div class="scroll-down"><svg width="16" height="10" viewBox="0 0 16 10"><path d="M2 2 L8 8 L14 2" fill="none" stroke="#fff" stroke-width="2.5"/></svg></div>

<footer class="site-footer">
  <div class="footer-brand">
    <div class="brand-name">TRAVENOK</div>
    <div class="brand-tag">PROJECT MANAGEMENT CONSULTATION</div>
    <div class="socials"><span></span><span></span><span></span><span></span><span></span></div>
  </div>

  <div class="footer-col contact-col">
    <h3>CONTACT US</h3>
    <div class="contact-item"><span class="contact-icon"><svg width="10" height="14" viewBox="0 0 10 14"><path d="M5 13 C1 8 1 6 1 5 A4 4 0 0 1 9 5 C9 6 9 8 5 13Z" fill="#fff"/></svg></span><p><b>TRAVENOKTECH</b><br>418 Harbor Vale Road, San Francisco, CA 94107</p></div>
    <div class="contact-item"><span class="contact-icon"><svg width="12" height="12" viewBox="0 0 12 12"><path d="M2 1 L4.5 1 L5.5 4 L4 5 C5 7 6 8 7 8 L8 6.5 L11 7.5 L11 10 C6 11 1 6 2 1Z" fill="#fff"/></svg></span><p><b>PHONE:</b><br>415 555 0192</p></div>
    <div class="contact-item"><span class="contact-icon"><svg width="12" height="10" viewBox="0 0 12 10"><rect x="1" y="1" width="10" height="8" fill="none" stroke="#fff" stroke-width="1.4"/><path d="M1 1 L6 5.5 L11 1" fill="none" stroke="#fff" stroke-width="1.4"/></svg></span><p><b>Mail:</b><br>office@travenoktech.example</p></div>
  </div>

  <div class="footer-col links-col">
    <h3>QUICK CONTACT</h3>
    <ul><li>Home</li><li>Professionals</li><li>Employers</li><li>Sign In</li><li>Sign Up</li><li>Contact Us</li></ul>
  </div>

  <div class="footer-col form-col">
    <h3>CONTACT FORM</h3>
    <div class="form-row"><div class="input">Name</div><div class="input">Phone</div></div>
    <div class="textarea">Message</div>
    <div class="btn">SEND MESSAGE</div>
  </div>

  <div class="footer-bar">Copyright © 2016 TravenokTech. All Right Reserved</div>
</footer>
</body>
</html>
```